RTavenor Business Cards & Letterhead

I have a logo but need a design for some new business cards. We are a Design-Build Firm that specializes in the design and construction of commercial projects.
the cards need to be professional. no cartoon stuff.
i would like to have the cards in AI format so I can update the card as needed. Logo is provided.
Our Address is: 4187 Marlowe Ct. Apex, North Carolina 27614

```html
<!DOCTYPE html>
<html lang="en">
<head>
<meta charset="utf-8">
<title>RTavenor Business Card</title>
<link rel="stylesheet" href="https://fonts.googleapis.com/css2?family=Montserrat:wght@700&family=Open+Sans:wght@400;600;700&display=swap">
<style>
  :root {
    --scene-bg: #232323;
    --card-bg: #1f2026;
    --card-edge: #1b7bcc;
    --brand-blue: #1c7fcf;
    --dot-blue: #1a64a6;
    --text-white: #ffffff;
    --mark-grey: #7b7d82;
  }
  * { margin: 0; padding: 0; box-sizing: border-box; }
  html, body { width: 1200px; height: 780px; overflow: hidden; background: var(--scene-bg); }
  .canvas { position: relative; width: 1200px; height: 780px; }
  .card {
    position: absolute; top: 70px; width: 400px; height: 640px;
    background: var(--card-bg); border-radius: 26px;
    border: 3px solid var(--card-edge);
    box-shadow: 0 18px 40px rgba(0,0,0,.55);
    overflow: hidden;
  }
  .card--back { left: 150px; }
  .card--front { left: 650px; }

  .back-wordmark {
    position: absolute; left: 50%; top: 50%;
    transform: translate(-50%, -50%) rotate(90deg);
    display: flex; align-items: center; gap: 18px;
    font-family: "Montserrat", sans-serif; font-weight: 700;
    font-size: 74px; letter-spacing: 4px; color: var(--mark-grey);
    white-space: nowrap;
  }
  .back-wordmark .brand-square { width: 46px; height: 46px; background: var(--brand-blue); }

  .front-brand {
    position: absolute; top: 80px; left: 0; right: 0;
    display: flex; flex-direction: column; align-items: center; gap: 18px;
  }
  .front-brand .brand-square { width: 120px; height: 120px; background: var(--brand-blue); border-radius: 8px; }
  .front-brand .brand-name {
    font-family: "Open Sans", sans-serif; font-weight: 700;
    font-size: 30px; letter-spacing: 3px; color: var(--brand-blue);
  }

  .contact { position: absolute; left: 0; right: 0; top: 330px; text-align: center; font-family: "Open Sans", sans-serif; color: var(--text-white); }
  .contact__name { font-weight: 700; font-size: 28px; color: var(--brand-blue); letter-spacing: .5px; }
  .contact__title { font-weight: 600; font-size: 17px; margin-top: 2px; }
  .dot-row { display: block; margin: 10px auto; }
  .contact__lines { font-size: 16px; line-height: 1.35; }
  .contact__address { font-size: 17px; line-height: 1.35; }
</style>
</head>
<body>
<main class="canvas">
  <section class="card card--back" aria-label="Card back">
    <div class="back-wordmark"><span class="brand-square"></span><span class="brand-name">RTAVENOR</span></div>
  </section>

  <section class="card card--front" aria-label="Card front">
    <div class="front-brand">
      <span class="brand-square"></span>
      <span class="brand-name">RTAVENOR</span>
    </div>

    <div class="contact">
      <div class="contact__name">GARRETT TAVENOR</div>
      <div class="contact__title">Founder/President</div>

      <svg class="dot-row" width="360" height="30" viewBox="0 0 360 30" aria-hidden="true">
        <g fill="var(--dot-blue)">
          <circle cx="10" cy="15" r="3"/><circle cx="28" cy="15" r="4"/><circle cx="48" cy="15" r="5"/><circle cx="70" cy="15" r="6"/><circle cx="94" cy="15" r="7"/><circle cx="118" cy="15" r="7.5"/>
          <circle cx="242" cy="15" r="7.5"/><circle cx="266" cy="15" r="7"/><circle cx="290" cy="15" r="6"/><circle cx="312" cy="15" r="5"/><circle cx="332" cy="15" r="4"/><circle cx="350" cy="15" r="3"/>
        </g>
        <g>
          <circle cx="148" cy="15" r="13" fill="var(--brand-blue)"/>
          <path d="M143 9 l3 0 l1 4 l-2 1.5 a9 9 0 0 0 4 4 l1.5 -2 l4 1 l0 3 a2 2 0 0 1 -2 1.5 a14 14 0 0 1 -11 -11 a2 2 0 0 1 1.5 -2z" fill="#fff"/>
          <circle cx="180" cy="15" r="13" fill="var(--brand-blue)"/>
          <rect x="172" y="9" width="16" height="12" rx="1" fill="none" stroke="#fff" stroke-width="1.6"/>
          <path d="M172 9 l8 7 l8 -7" fill="none" stroke="#fff" stroke-width="1.6"/>
          <circle cx="212" cy="15" r="13" fill="var(--brand-blue)"/>
          <circle cx="212" cy="15" r="7.5" fill="none" stroke="#fff" stroke-width="1.6"/>
          <path d="M204.5 15 h15 M212 7.5 c-4 4 -4 11 0 15 M212 7.5 c4 4 4 11 0 15" fill="none" stroke="#fff" stroke-width="1.2"/>
        </g>
      </svg>

      <div class="contact__lines">
        <div>(919) 555-0148</div>
        <div>www.rtavenor.com</div>
        <div>GT@RTavenor.com</div>
      </div>

      <svg class="dot-row" width="360" height="30" viewBox="0 0 360 30" aria-hidden="true">
        <g fill="var(--dot-blue)">
          <circle cx="10" cy="15" r="3"/><circle cx="28" cy="15" r="4"/><circle cx="48" cy="15" r="5"/><circle cx="70" cy="15" r="6"/><circle cx="94" cy="15" r="7"/><circle cx="120" cy="15" r="7.5"/><circle cx="146" cy="15" r="8"/>
          <circle cx="214" cy="15" r="8"/><circle cx="240" cy="15" r="7.5"/><circle cx="266" cy="15" r="7"/><circle cx="290" cy="15" r="6"/><circle cx="312" cy="15" r="5"/><circle cx="332" cy="15" r="4"/><circle cx="350" cy="15" r="3"/>
        </g>
        <circle cx="180" cy="15" r="13" fill="var(--brand-blue)"/>
        <path d="M180 24 c-5 -6 -6 -8.5 -6 -11 a6 6 0 0 1 12 0 c0 2.5 -1 5 -6 11z" fill="#fff"/>
        <circle cx="180" cy="13" r="2.3" fill="var(--brand-blue)"/>
      </svg>

      <div class="contact__address">
        <div>4187 Marlowe Ct. Apex,</div>
        <div>North Carolina 27614</div>
      </div>
    </div>
  </section>
</main>
</body>
</html>
```